Etikett für einen Rosé Wein
Zielgruppe
Wir sind ein Weingut und benötigen ein neues Etikett für unseren Muskattrollinger Rosé. Unsere Kunden sind eher traditionelle Weinkäufer.
Aufgabenstellung
Format:
Höhe: 9 cm
Breite: 11 cm
Da es nur ein Vorderetikett gibt, müssen alle relevanten Angaben (Hersteller, Alkohol, Inhalt in L, Rebsorte, etc.) enthalten sein. (siehe Flaschenabbildung anbei)
WÜRTTEMBERG
2019er
Muskattrollinger Rosé
DEUTSCHER QUALITÄTSWEIN
11,0 % Vol.
0,75 l
Enthält Sulfite
A.P.Nr. 58127364
Abfüller
Straße / PLZ / Ort / Tel.
Der Flaschenverschluss ist schwarz d.h. das neue Etikettendesign sollte dazu passen.
Bisher ist der Hintergrund des Weinetiketts schwarz. Dies muss jedoch nicht so bleiben.
Im Anhang finden Sie außerdem ein Plakat. Ggf. können Sie für das Flaschendesign einige nostalgische Elemente davon übernehmen.

```html
<!DOCTYPE html>
<html lang="de">
<head>
<meta charset="utf-8">
<title>Muskattrollinger Rosé – Etikett</title>
<link rel="stylesheet" href="https://fonts.googleapis.com/css2?family=Old+Standard+TT&family=Questrial&display=swap">
<style>
  :root {
    --stage: #d9d9d9;
    --paper-light: #ffffff;
    --ink-light: #1a1a1a;
    --art-light: #d4d4d4;
    --paper-dark: #000000;
    --ink-dark: #f2f2f2;
    --art-dark: #363636;
  }
  * { margin: 0; padding: 0; box-sizing: border-box; }
  html, body { width: 1200px; height: 799px; overflow: hidden; }
  body { background: var(--stage); position: relative; }

  .label {
    position: absolute;
    top: 170px;
    width: 560px;
    height: 458px;
    font-family: "Questrial", "Helvetica Neue", sans-serif;
  }
  .label--light { left: 30px; background: var(--paper-light); color: var(--ink-light); --art: var(--art-light); }
  .label--dark  { left: 610px; background: var(--paper-dark); color: var(--ink-dark); --art: var(--art-dark); }

  .label > * { position: absolute; }

  .label__art { background: var(--art); }
  .label__art--grapes  { left: 158px; top: 26px; width: 52px; height: 56px; border-radius: 40%; }
  .label__art--berries { left: 352px; top: 26px; width: 54px; height: 56px; border-radius: 40%; }
  .label__art--roses   { left: 165px; top: 182px; width: 237px; height: 130px; border-radius: 30% 30% 50% 50%; }

  .label__region { left: 0; right: 0; top: 14px; text-align: center; font-size: 17px; line-height: 20px; letter-spacing: 0.3px; }
  .label__vintage { left: 0; right: 0; top: 40px; text-align: center; font-size: 14px; line-height: 17px; }

  .label__title {
    left: 0; right: 0; top: 90px; text-align: center;
    font-family: "Old Standard TT", "Bodoni 72", serif;
    font-weight: 400; font-size: 39px; line-height: 43px;
  }

  .label__alcohol { left: 134px; top: 382px; width: 50px; text-align: center; font-size: 13px; line-height: 17px; }
  .label__quality { left: 202px; top: 391px; font-size: 12px; line-height: 14px; letter-spacing: 0.2px; }
  .label__volume  { left: 390px; top: 388px; font-size: 13px; line-height: 16px; }

  .label__legal {
    left: 0; right: 0; top: 416px; text-align: center;
    font-size: 6.5px; line-height: 8.5px;
  }
</style>
</head>
<body>

<section class="label label--light" aria-label="Weinetikett, helle Variante">
  <div class="label__art label__art--grapes" role="img" aria-label="Gravur einer Weintraube mit Blatt"></div>
  <div class="label__art label__art--berries" role="img" aria-label="Gravur von Beeren mit Blättern"></div>
  <p class="label__region">WÜRTTEMBERG</p>
  <p class="label__vintage">2019er</p>
  <h1 class="label__title">Muskattrollinger<br>Rosé</h1>
  <div class="label__art label__art--roses" role="img" aria-label="Gravur eines Rosenbouquets mit Blättern"></div>
  <p class="label__alcohol">11,0 %<br>Vol.</p>
  <p class="label__quality">DEUTSCHER QUALITÄTSWEIN</p>
  <p class="label__volume">0,75 l</p>
  <p class="label__legal">A.P.Nr. 58127364<br>Abfüller D-KLM 512<br>vermarket durch: Lukas Wendler Straße / PLZ / Ort / Tel.</p>
</section>

<section class="label label--dark" aria-label="Weinetikett, dunkle Variante">
  <div class="label__art label__art--grapes" role="img" aria-label="Gravur einer Weintraube mit Blatt"></div>
  <div class="label__art label__art--berries" role="img" aria-label="Gravur von Beeren mit Blättern"></div>
  <p class="label__region">WÜRTTEMBERG</p>
  <p class="label__vintage">2019er</p>
  <h2 class="label__title">Muskattrollinger<br>Rosé</h2>
  <div class="label__art label__art--roses" role="img" aria-label="Gravur eines Rosenbouquets mit Blättern"></div>
  <p class="label__alcohol">11,0 %<br>Vol.</p>
  <p class="label__quality">DEUTSCHER QUALITÄTSWEIN</p>
  <p class="label__volume">0,75 l</p>
  <p class="label__legal">A.P.Nr. 58127364<br>Abfüller D-KLM 512<br>vermarket durch: Lukas Wendler Straße / PLZ / Ort / Tel.</p>
</section>

</body>
</html>
```